Bref créative
Business cards and stationary Hospitality group company in Mexico
subtitle is optional "Hospitalidad Hecho en Mexico"
I need double sided standard sized Business Card [3.5" x 2"]
I like the fonts used in my logo but we are open to new fonts or more than one if necessary
Modern
Armando Quiroz
4817 Almendros
Col. Brisa Verde
Monterrey, NL México
CP 58213
tavo@qelun.mx
www.qelun.mx
I am looking for a modern design, I like those colors but feel free to play with the colors if you have an idea..
RV DELCANTO

```html
<!DOCTYPE html>
<html lang="es">
<head>
<meta charset="utf-8">
<title>RV Delcanto — Papelería</title>
<link rel="stylesheet" href="https://fonts.googleapis.com/css2?family=Montserrat:wght@500;700&family=Open+Sans:wght@400;600&display=swap">
<style>
  :root {
    --paper: #ffffff;
    --backdrop: #eceded;
    --ink: #2c2b2b;
    --orange: #f0491f;
    --orange-light: #f4703d;
    --muted: #8a8a8a;
    --faint: #f6d9cf;
  }
  * { box-sizing: border-box; margin: 0; padding: 0; }
  html, body { width: 1200px; height: 936px; overflow: hidden; }
  body {
    background: var(--backdrop);
    font-family: "Open Sans", Arial, sans-serif;
    position: relative;
  }
  .sheet { position: absolute; background: var(--paper); overflow: hidden; }

  .brand {
    font-family: "Montserrat", Arial, sans-serif;
    font-weight: 700;
    color: var(--orange);
    letter-spacing: 0.04em;
    white-space: nowrap;
    display: flex;
    align-items: center;
    gap: 6px;
  }
  .brand-dot { display: inline-block; background: var(--orange); }

  .contact-list { list-style: none; color: var(--muted); }
  .contact-list li { display: flex; align-items: center; gap: 5px; white-space: nowrap; }
  .contact-list .bullet { width: 5px; height: 5px; background: var(--orange); flex: none; }

  /* Letterhead */
  .letterhead { left: 38px; top: 36px; width: 409px; height: 566px; }
  .letterhead .header-band {
    position: absolute; left: 0; top: 0; width: 100%; height: 91px; background: var(--ink);
  }
  .letterhead .header-tab {
    position: absolute; left: 0; top: 20px; width: 8px; height: 50px; background: var(--orange);
  }
  .letterhead .brand { position: absolute; left: 22px; top: 36px; font-size: 15px; }
  .letterhead .brand-dot { width: 9px; height: 9px; }
  .letterhead .contact-list {
    position: absolute; left: 272px; top: 14px; font-size: 7px; line-height: 12px; color: #cfcfcf;
  }
  .letterhead .watermark {
    position: absolute; left: 0; right: 0; top: 278px; text-align: center;
    font-family: "Montserrat", Arial, sans-serif; font-weight: 700;
    font-size: 40px; letter-spacing: 0.06em; color: var(--faint);
  }

  /* Folder */
  .folder {
    left: 638px; top: 36px; width: 472px; height: 574px;
    background: radial-gradient(ellipse at 50% 55%, var(--orange-light), var(--orange) 75%);
  }
  .folder .cover-band {
    position: absolute; left: 0; top: 198px; width: 100%; height: 185px; background: var(--ink);
  }
  .folder .cover-tab {
    position: absolute; left: 0; top: 248px; width: 10px; height: 78px; background: var(--orange);
  }
  .folder .brand-block {
    position: absolute; left: 0; right: 0; top: 258px;
    display: flex; flex-direction: column; align-items: center; gap: 10px;
  }
  .folder .brand { font-size: 26px; }
  .folder .brand-dot { width: 14px; height: 14px; }
  .folder .tagline {
    font-family: "Montserrat", Arial, sans-serif; font-weight: 500;
    font-size: 9px; letter-spacing: 0.2em; color: #ffffff;
  }

  /* Business cards */
  .card { left: 41px; width: 183px; height: 106px; }
  .card-front { top: 663px; }
  .card-front .card-top {
    position: absolute; left: 0; top: 0; width: 100%; height: 44px; background: var(--ink);
  }
  .card-front .brand { position: absolute; left: 10px; top: 16px; font-size: 10px; }
  .card-front .brand-dot { width: 6px; height: 6px; }
  .card-front .contact-list {
    position: absolute; left: 10px; top: 52px; font-size: 5.5px; line-height: 8px;
  }
  .card-front .person {
    position: absolute; right: 10px; top: 80px;
    font-family: "Montserrat", Arial, sans-serif; font-weight: 700;
    font-size: 7px; color: var(--orange);
  }
  .card-back { top: 785px; height: 104px; background: var(--ink); }
  .card-back .brand { position: absolute; left: 12px; top: 38px; font-size: 11px; }
  .card-back .brand-dot { width: 6px; height: 6px; }
  .card-back .site {
    position: absolute; left: 12px; top: 78px; font-size: 6px; letter-spacing: 0.2em; color: var(--orange);
  }

  /* Envelopes */
  .envelope { top: 673px; height: 208px; }
  .envelope-front { left: 262px; width: 437px; }
  .envelope-front .top-band {
    position: absolute; left: 0; top: 0; width: 100%; height: 44px; background: var(--ink);
  }
  .envelope-front .brand { position: absolute; left: 14px; top: 15px; font-size: 11px; }
  .envelope-front .brand-dot { width: 7px; height: 7px; }
  .envelope-front .return-address {
    position: absolute; left: 14px; top: 52px; font-size: 6px; color: var(--muted); white-space: nowrap;
  }
  .envelope-back { left: 739px; width: 429px; }
  .envelope-back .flap { position: absolute; left: 0; top: 0; }
  .envelope-back .site {
    position: absolute; left: 0; right: 0; top: 22px; text-align: center;
    font-family: "Montserrat", Arial, sans-serif; font-weight: 500;
    font-size: 13px; letter-spacing: 0.25em; color: #ffffff;
  }
</style>
</head>
<body>

  <section class="sheet letterhead">
    <div class="header-band"></div>
    <div class="header-tab"></div>
    <div class="brand"><span class="brand-dot"></span>RV DELCANTO</div>
    <ul class="contact-list">
      <li><span class="bullet"></span>4817 Almendros, Col. Brisa Verde</li>
      <li><span class="bullet"></span>Monterrey, NL México CP 58213</li>
      <li><span class="bullet"></span>+52 81 4402 7719</li>
      <li><span class="bullet"></span>tavo@qelun.mx</li>
      <li><span class="bullet"></span>www.qelun.mx</li>
    </ul>
    <div class="watermark">RV DELCANTO</div>
  </section>

  <section class="sheet folder">
    <div class="cover-band"></div>
    <div class="cover-tab"></div>
    <div class="brand-block">
      <div class="brand"><span class="brand-dot"></span>RV DELCANTO</div>
      <div class="tagline">HOSPITALIDAD HECHO EN MÉXICO</div>
    </div>
  </section>

  <section class="sheet card card-front">
    <div class="card-top"></div>
    <div class="brand"><span class="brand-dot"></span>RV DELCANTO</div>
    <ul class="contact-list">
      <li>4817 Almendros</li>
      <li>Col. Brisa Verde</li>
      <li>CP 58213</li>
      <li>tavo@qelun.mx</li>
    </ul>
    <div class="person">Armando Quiroz</div>
  </section>

  <section class="sheet card card-back">
    <div class="brand"><span class="brand-dot"></span>RV DELCANTO</div>
    <div class="site">www.qelun.mx</div>
  </section>

  <section class="sheet envelope envelope-front">
    <div class="top-band"></div>
    <div class="brand"><span class="brand-dot"></span>RV DELCANTO</div>
    <p class="return-address">4817 Almendros, Col. Brisa Verde, Monterrey, NL México, CP 58213</p>
  </section>

  <section class="sheet envelope envelope-back">
    <svg class="flap" width="429" height="208" viewBox="0 0 429 208" aria-hidden="true">
      <defs>
        <linearGradient id="flapFill" x1="0" y1="0" x2="0" y2="1">
          <stop offset="0" stop-color="#f4703d"/>
          <stop offset="1" stop-color="#f0491f"/>
        </linearGradient>
      </defs>
      <path d="M0 0 H429 V56 Q214 96 0 56 Z" fill="url(#flapFill)"/>
      <path d="M0 56 Q214 96 429 56" fill="none" stroke="#d9d9d9" stroke-width="1"/>
    </svg>
    <div class="site">www.qelun.mx</div>
  </section>

</body>
</html>
```